Pepper & Palm Business Card FUN & EXCITING

Here is the Information for the Card:
Jaswinder Bains (Ravi)
E: RaviBains@postlark.com
C: (480) 555-0147
www.PepperPalmLV.com

We don't want traditional Indian cliche, We a playful bold and fun business card.

Files: https://files.cloudvessel.net/share/folders/7TqRmXpZ2vKa9LwBn4YcHd3JsEf6UoGi?usp=share_link

https://files.cloudvessel.net/share/folders/4MzXaQ8rTw2YbNcVk6PsLe5GhJdR3FoU?usp=share_link

Target Market(s)

Las Vegas Local Restaurant

Industry/Entity Type

Indian Restaurant

Contact Information for Business Card

Name, Email, Cell Phone, Company Logo

```html
<!DOCTYPE html>
<html lang="en">
<head>
<meta charset="UTF-8">
<title>Pepper &amp; Palm – Business Card</title>
<link rel="stylesheet" href="https://fonts.googleapis.com/css2?family=Oswald:wght@600;700&family=Open+Sans:wght@400;600&display=swap">
<style>
  :root {
    --backdrop: #232323;
    --mustard: #F2C516;
    --pink: #E01E5A;
    --teal: #17A88F;
    --cream: #FCFBF1;
    --ink: #1E1E1E;
    --photo-red: #B3202A;
    --photo-green: #3E8E2F;
  }
  * { margin: 0; padding: 0; box-sizing: border-box; }
  html, body {
    width: 1200px; height: 780px; overflow: hidden;
    background: var(--backdrop);
  }
  .canvas {
    position: relative; width: 1200px; height: 780px;
    display: flex; justify-content: center; align-items: center; gap: 80px;
  }
  .card {
    position: relative; width: 330px; height: 576px;
    border-radius: 30px; overflow: hidden;
    box-shadow: 0 18px 40px rgba(0,0,0,.55);
  }

  /* Front */
  .card-front {
    background: var(--mustard);
    display: flex; justify-content: center; align-items: center;
  }
  .front-brand {
    transform: rotate(-90deg);
    white-space: nowrap;
    font-family: "Oswald", sans-serif; font-weight: 700;
    font-size: 78px; letter-spacing: 2px; text-transform: uppercase;
    color: var(--pink);
  }

  /* Back */
  .card-back { background: var(--cream); }
  .back-brand {
    margin-top: 52px; text-align: center;
    font-family: "Oswald", sans-serif; font-weight: 700;
    font-size: 46px; line-height: 1; text-transform: uppercase;
    color: var(--pink);
  }
  .holder-name {
    margin-top: 46px; text-align: center;
    font-family: "Oswald", sans-serif; font-weight: 600;
    font-size: 25px; letter-spacing: .3px; text-transform: uppercase;
    color: var(--pink);
  }
  .contact-icons {
    margin-top: 16px; display: flex; justify-content: center; gap: 8px;
  }
  .icon-dot {
    width: 28px; height: 28px; border-radius: 50%;
    background: var(--teal);
    display: flex; align-items: center; justify-content: center;
  }
  .icon-dot svg { width: 15px; height: 15px; }
  .contact-lines, .address {
    text-align: center;
    font-family: "Open Sans", sans-serif; font-size: 14.5px;
    line-height: 1.45; color: var(--ink);
  }
  .contact-lines { margin-top: 10px; }
  .pin-row { margin-top: 14px; display: flex; justify-content: center; }
  .address { margin-top: 8px; position: relative; z-index: 2; }

  .food-band {
    position: absolute; left: 0; right: 0; bottom: 0; height: 190px;
  }
  .food-photo {
    position: absolute; inset: 0;
    background:
      radial-gradient(circle at 30% 70%, var(--photo-green) 0 18%, transparent 40%),
      radial-gradient(circle at 75% 40%, var(--photo-green) 0 14%, transparent 36%),
      linear-gradient(135deg, #C72B3A, var(--photo-red) 55%, #7E1A1E);
  }
  .food-curve {
    position: absolute; left: 0; top: 0; width: 100%; height: 100%;
  }
</style>
</head>
<body>
<main class="canvas">

  <section class="card card-front" aria-label="Card front">
    <div class="front-brand">Pepper &amp; Palm</div>
  </section>

  <section class="card card-back" aria-label="Card back">
    <div class="back-brand">Pepper &amp;<br>Palm</div>

    <div class="holder-name">Jaswinder Bains (Ravi)</div>

    <div class="contact-icons">
      <span class="icon-dot" aria-label="Phone">
        <svg viewBox="0 0 24 24" fill="#fff"><path d="M6.6 10.8a15 15 0 0 0 6.6 6.6l2.2-2.2c.3-.3.7-.4 1-.2 1.1.4 2.3.6 3.6.6.6 0 1 .4 1 1V20c0 .6-.4 1-1 1A17 17 0 0 1 3 4c0-.6.4-1 1-1h3.5c.6 0 1 .4 1 1 0 1.3.2 2.5.6 3.6.1.3 0 .7-.2 1z"/></svg>
      </span>
      <span class="icon-dot" aria-label="Email">
        <svg viewBox="0 0 24 24" fill="none" stroke="#fff" stroke-width="2"><rect x="3" y="5" width="18" height="14" rx="2"/><path d="M3 7l9 6 9-6"/></svg>
      </span>
      <span class="icon-dot" aria-label="Website">
        <svg viewBox="0 0 24 24" fill="none" stroke="#fff" stroke-width="2"><circle cx="12" cy="12" r="9"/><path d="M3 12h18M12 3c3 3 3 15 0 18M12 3c-3 3-3 15 0 18"/></svg>
      </span>
    </div>

    <div class="contact-lines">
      (480) 555-0147<br>
      RaviBains@postlark.com<br>
      www.PepperPalmLV.com
    </div>

    <div class="pin-row">
      <span class="icon-dot" aria-label="Location">
        <svg viewBox="0 0 24 24" fill="none" stroke="#fff" stroke-width="2"><path d="M12 21s-6-6.2-6-11a6 6 0 0 1 12 0c0 4.8-6 11-6 11z"/><circle cx="12" cy="10" r="2.2"/></svg>
      </span>
    </div>

    <div class="address">
      1180 Desert Bloom Pkwy, Suite #214,<br>
      Henderson, NV 89011
    </div>

    <div class="food-band">
      <div class="food-photo" role="img" aria-label="Close-up photo of a red curry dish topped with fresh coriander and red onion"></div>
      <svg class="food-curve" viewBox="0 0 330 190" preserveAspectRatio="none" aria-hidden="true">
        <defs>
          <filter id="curve-shadow" x="-10%" y="-10%" width="120%" height="140%">
            <feDropShadow dx="0" dy="6" stdDeviation="6" flood-color="#000" flood-opacity=".28"/>
          </filter>
        </defs>
        <path d="M0 0 H330 V20 C290 110 140 125 0 70 Z" fill="#E6E4DA"/>
        <path d="M0 0 H330 V0 C300 80 150 105 0 55 Z" fill="var(--cream)" filter="url(#curve-shadow)"/>
      </svg>
    </div>
  </section>

</main>
</body>
</html>
```